6 page suburb profile/report for real estate agent to provide to clients

I would like a suburb report to be created in our corporate colours and branding for a local Geelong (Australia) based real estate agent.

The design should be fresh, clean and easy to read, not to cluttered. I dont want a corporate plain boring style.

All content and details are provided and the below link provides a bunch of stock photos that can be used. If you prefer to source some better images from pixmora or framevaultly im happy for them to be ripped and used as low res and if you win the job i will then purchase the images and supply hi res.

I have also included a couple of sample reports produced by other organisations and style/brand guides for our corporation.

The word doc attached has all content to be included and also some notes for your reference. There are a variety of charts to be created (all data provided in word doc), the notes indicating the type/style of chart to be used is a guide only. If you feel you can create a better design/layout using different formats/styles thats fine by me.

If you win the job i will need a further 12 reports produced using the style/format. It will be a case of updating the stats/figures for each report.

If you have any questions regarding the project please dont hesitate to contact me.

6 page document
Page size: A4 Portrait (297mm H x210mm W)
Bleed design off the page
Artwork to setup 100% CMYK
Print ready PDF and live/working files to be supplied
Attached are specs for a variety of programs depending on what you create the job in.
I will require a high res file for printing and also a lower res file suitebale for emailing to clients
Revisions will be required before final files supplied

Stock images
https://www.filecrate-share.example/sh/q7rt2lm9xz4kpw1/BBXQLOWd8RT51Hn4Kc2_Z9pb?dl=0

Target Market(s)

Property owners, property investors, people interested in buying and selling property

Industry/Entity Type

Real Estate Agent

Font styles to use
Serif
Sans Serif
Other font styles liked:
• Source Sans Pro is the corporate font

Colors
0692cd
33a6d7
85cae6
cee9f5
cdddec
85abd2
3176b5
0355a3

Requirements
Must have
• Statistical content provided
• Corporate logo
• Corporate colours - can be creative but dont want a birght happy colour rainbow of colours
Should not have
• Must not represent other real estate agencies corporate colours

```html
<!DOCTYPE html>
<html lang="en">
<head>
<meta charset="utf-8">
<title>Hamlyn Heights VIC 3215 – Suburb Insights</title>
<link rel="stylesheet" href="https://fonts.googleapis.com/css2?family=Source+Sans+3:wght@300;400;600&display=swap">
<style>
  :root {
    --blue-strong: #0692cd;
    --blue-mid: #33a6d7;
    --blue-light: #85cae6;
    --blue-pale: #cee9f5;
    --blue-steel: #3176b5;
    --blue-sky: #9dcdee;
    --band: #ebf3fa;
    --ink: #1d1d1f;
    --ink-soft: #333;
    --paper: #ffffff;
  }
  * { box-sizing: border-box; margin: 0; padding: 0; }
  html, body { width: 867px; height: 1200px; overflow: hidden; background: var(--paper); }
  body { font-family: "Source Sans 3", "Source Sans Pro", sans-serif; color: var(--ink); }

  .page { position: relative; width: 867px; height: 1200px; background: var(--paper); overflow: hidden; }

  .header { position: absolute; left: 0; top: 0; width: 867px; height: 195px; display: block; }

  .intro { position: absolute; left: 40px; top: 296px; width: 377px; }
  .intro h1 { font-weight: 400; font-size: 28px; line-height: 34px; color: var(--ink); }
  .intro .subtitle { font-weight: 300; font-size: 28px; line-height: 34px; color: var(--blue-mid); margin-bottom: 26px; }
  .intro p { font-size: 15.5px; line-height: 22.8px; font-weight: 300; color: var(--ink-soft); text-align: justify; margin-bottom: 22px; }

  .map { position: absolute; left: 451px; top: 276px; width: 378px; height: 410px;
    background: linear-gradient(135deg, #efe6dc 0%, #f3ece4 45%, #e3eedb 80%, #d8e9d2 100%); }

  .demographics { position: absolute; left: 0; top: 731px; width: 867px; height: 469px; background: var(--band); }
  .demographics h2 { position: absolute; left: 40px; top: 19px; font-weight: 400; font-size: 28px; line-height: 34px; color: var(--ink); }

  .section-title { position: absolute; font-weight: 300; font-size: 24px; line-height: 28px; color: var(--blue-mid);
    border-bottom: 1.5px solid var(--blue-mid); padding-bottom: 2px; }
  .dwelling-title { left: 40px; top: 69px; width: 376px; }
  .tenure-title { left: 40px; top: 244px; width: 376px; }
  .population-title { left: 451px; top: 70px; width: 376px; }

  .pie { position: absolute; width: 120px; height: 120px; }
  .dwelling-pie { left: 40px; top: 105px; }
  .tenure-pie { left: 40px; top: 283px; }

  .legend { position: absolute; font-size: 12.5px; line-height: 17px; color: var(--ink-soft); font-weight: 400; }
  .legend li { list-style: none; display: flex; justify-content: space-between; }
  .dwelling-legend { left: 183px; top: 131px; width: 233px; }
  .tenure-legend { left: 185px; top: 299px; width: 233px; }

  .population-chart { position: absolute; left: 451px; top: 108px; width: 380px; height: 330px; display: block; }
  .population-chart text { font-family: "Source Sans 3", "Source Sans Pro", sans-serif; fill: var(--ink-soft); }

  .folio { position: absolute; left: 0; top: 1167px; width: 867px; display: flex; justify-content: center; align-items: center; gap: 10px;
    font-size: 12px; font-weight: 600; color: var(--ink); }
  .folio::before, .folio::after { content: ""; width: 34px; height: 2px; background: var(--blue-strong); }
</style>
</head>
<body>
<main class="page">

  <svg class="header" viewBox="0 0 800 184" preserveAspectRatio="none">
    <defs>
      <linearGradient id="photo-tone" x1="0" y1="0" x2="1" y2="1">
        <stop offset="0" stop-color="#cfc9c3"/>
        <stop offset="0.35" stop-color="#e8ebe4"/>
        <stop offset="0.7" stop-color="#8d9097"/>
        <stop offset="1" stop-color="#3d5d8e"/>
      </linearGradient>
    </defs>
    <rect width="800" height="184" fill="url(#photo-tone)" role="img" aria-label="Photograph of a coffee plunger, white roses and blue cups in front of striped cushions"/>
    <polygon points="433,184 603,0 800,0 800,184" fill="var(--blue-sky)"/>
    <polygon points="433,184 603,0 630,0 460,184" fill="var(--paper)"/>
    <polygon points="590,184 760,0 785,0 615,184" fill="var(--paper)"/>
    <polygon points="750,184 800,130 800,160 778,184" fill="var(--paper)"/>
  </svg>

  <section class="intro">
    <h1>Hamlyn Heights VIC 3215</h1>
    <div class="subtitle">Suburb Insights</div>
    <p>The size of Hamlyn Heights is approximately 4 square kilometres. It has 6 parks covering nearly 3% of total area.</p>
    <p>The population of Hamlyn Heights in 2006 was 5,838 people, by 2011 the population was 6,078 showing a population growth of 4% in the area during that time. Households in Hamlyn Heights are primarily couples with children and are likely to be repaying between $1400-$1800 per month on mortgage repayments.</p>
    <p>In 2011 74% of homes were owner-occupied, slightly down when compared to 75.3% in 2006.</p>
  </section>

  <div class="map" role="img" aria-label="Street map of Hamlyn Heights and surrounding streets"></div>

  <section class="demographics">
    <h2>Demographics</h2>

    <h3 class="section-title dwelling-title">Dwelling Type</h3>
    <svg class="pie dwelling-pie" viewBox="-60 -60 120 120" role="img" aria-label="Dwelling type pie chart">
      <g stroke="var(--paper)" stroke-width="1.5" stroke-linejoin="round">
        <path d="M0 0 L43.15 35.69 A56 56 0 1 1 56 0 Z" fill="var(--blue-steel)"/>
        <path d="M0 0 L56 0 A56 56 0 0 1 52.46 19.61 Z" fill="var(--blue-mid)"/>
        <path d="M0 0 L52.46 19.61 A56 56 0 0 1 43.15 35.69 Z" fill="var(--blue-strong)"/>
      </g>
    </svg>
    <ul class="legend dwelling-legend">
      <li><span>Separate house:</span><span>2142</span></li>
      <li><span>Semi-detached (row/terrace):</span><span>137</span></li>
      <li><span>Flat, unit or apartment:</span><span>128</span></li>
      <li><span>Other:</span><span>0</span></li>
    </ul>

    <h3 class="section-title tenure-title">Rent vs. Own</h3>
    <svg class="pie tenure-pie" viewBox="-60 -60 120 120" role="img" aria-label="Rent versus own pie chart">
      <g stroke="var(--paper)" stroke-width="1.5" stroke-linejoin="round">
        <path d="M0 0 L-53.72 -15.81 A56 56 0 0 1 55.25 -9.15 Z" fill="var(--blue-steel)"/>
        <path d="M0 0 L55.25 -9.15 A56 56 0 0 1 55.80 -4.69 Z" fill="var(--blue-light)"/>
        <path d="M0 0 L55.80 -4.69 A56 56 0 0 1 55.91 -3.22 Z" fill="var(--blue-pale)"/>
        <path d="M0 0 L55.91 -3.22 A56 56 0 0 1 14.30 54.14 Z" fill="var(--blue-mid)"/>
        <path d="M0 0 L14.30 54.14 A56 56 0 0 1 -53.72 -15.81 Z" fill="var(--blue-strong)"/>
      </g>
    </svg>
    <ul class="legend tenure-legend">
      <li><span>Own:</span><span>996</span></li>
      <li><span>Purchasing:</span><span>783</span></li>
      <li><span>Rent government:</span><span>30</span></li>
      <li><span>Rent private:</span><span>507</span></li>
      <li><span>Other:</span><span>10</span></li>
    </ul>

    <h3 class="section-title population-title">Population</h3>
    <svg class="population-chart" viewBox="0 0 380 330" role="img" aria-label="Population by age and sex">
      <g font-size="18" text-anchor="middle">
        <text x="144" y="19">Male</text>
        <text x="255" y="19">Female</text>
      </g>
      <g fill="var(--blue-light)">
        <rect x="51" y="31" width="112" height="21"/>
        <rect x="120" y="71" width="43" height="21"/>
        <rect x="114" y="111" width="49" height="21"/>
        <rect x="114" y="152" width="49" height="21"/>
        <rect x="124" y="192" width="39" height="21"/>
        <rect x="136" y="232" width="27" height="21"/>
        <rect x="131" y="271" width="32" height="21"/>
      </g>
      <g fill="var(--blue-strong)">
        <rect x="226" y="31" width="98" height="21"/>
        <rect x="226" y="71" width="55" height="21"/>
        <rect x="226" y="111" width="74" height="21"/>
        <rect x="226" y="152" width="70" height="21"/>
        <rect x="226" y="192" width="53" height="21"/>
        <rect x="226" y="232" width="35" height="21"/>
        <rect x="226" y="271" width="72" height="21"/>
      </g>
      <g font-size="16" text-anchor="middle">
        <text x="194" y="47">0-24</text>
        <text x="194" y="87">25-34</text>
        <text x="194" y="127">35-44</text>
        <text x="194" y="168">45-54</text>
        <text x="194" y="208">55-64</text>
        <text x="194" y="248">65-74</text>
        <text x="194" y="287">75+</text>
      </g>
      <g font-size="16" text-anchor="end">
        <text x="46" y="47">934</text>
        <text x="115" y="87">360</text>
        <text x="109" y="127">408</text>
        <text x="109" y="168">408</text>
        <text x="119" y="208">324</text>
        <text x="131" y="248">227</text>
        <text x="126" y="287">271</text>
      </g>
      <g font-size="16">
        <text x="328" y="35">898</text>
        <text x="285" y="87">394</text>
        <text x="304" y="127">438</text>
        <text x="300" y="168">409</text>
        <text x="283" y="208">323</text>
        <text x="265" y="248">254</text>
        <text x="302" y="287">428</text>
      </g>
    </svg>
  </section>

  <div class="folio">1</div>
</main>
</body>
</html>
```